Popup Nightclub Grand Opening Flyer

We need to design a flyer for the grand opening of an upscale, exclusive nightclub called "Lantern". The design needs to be chic and exclusive. The background should be black and the text should primarily be white. We like minimalist designs.

Here is the text for the flyer
-
Velvetroll Atlanta Presents

Lantern (LOGO)

A Popup Nightclub Experience
For one night Only

Friday, October 18, 2013
Party begins at 9PM

INVITE ONLY

See invitation for location details
(Velvetroll Atlanta logo)

-
Examples we like

http://cdn4-x.pressfolio-example.com/sites/default/files/styles/image_content_width/hash/3b/fd/2468013579_4421_flyer.jpg?itok=K9rtQw2z

http://files.hubspace-example.net/files/8Hqq-Tr72WWE3kaRbTmcxP5QZK2F396J8nbRw4CKMHfdX2Y7qSEF-MqjxDoNrLY3QCyQJD7npjGaRq3k-Mhx6hqf3MDSWf8r3/2zenSaturdays.jpg

http://morvex-example.com/wp-content/uploads/siteskin/widgetkit/gallery/2zen/2zen-gen_qstay4-01.jpg

Hi All, one thing that we are seeing that we don't like is on over emphasis on the phrase "a popup nightclub experience" please don't make this the largest thing on the flyer

Target Market(s)

Target market is 25-35 year olds who are affluent (rich) and like luxury brands

Requirements
Must have
• Dark Background
Nice to have
• Velvetroll Logo on the bottom
Modern text that isn't curvy
Should not have
• Curved text

```html
<!DOCTYPE html>
<html lang="en">
<head>
<meta charset="utf-8">
<title>Lantern Nightclub – Popup Night</title>
<link rel="stylesheet" href="https://fonts.googleapis.com/css2?family=Montserrat:wght@600;700&family=Questrial&display=swap">
<style>
  :root {
    --ink: #000000;
    --pattern-deep: #0a0a0a;
    --pattern-mid: #1c1c1c;
    --text-white: #ffffff;
    --text-soft: #e6e6e6;
    --text-grey: #8c8c8c;
    --rule: #9a9a9a;
    --accent-red: #ff2a1a;
    --accent-glow: rgba(255, 40, 20, 0.75);
    --mark-grey: #bdbdbd;
  }
  html, body {
    margin: 0;
    padding: 0;
    background: var(--ink);
    overflow: hidden;
  }
  .flyer {
    position: relative;
    width: 787px;
    height: 1200px;
    background: var(--ink);
    overflow: hidden;
    font-family: "Montserrat", Arial, sans-serif;
    color: var(--text-white);
    text-align: center;
  }
  .flyer__pattern {
    position: absolute;
    left: 0; top: 0;
    width: 787px;
    height: 760px;
    background: radial-gradient(ellipse at 50% 40%, var(--pattern-mid) 0%, var(--pattern-deep) 55%, var(--ink) 100%);
  }
  .flyer__block {
    position: absolute;
    left: 0;
    width: 100%;
    margin: 0;
  }
  .presenter {
    top: 46px;
    font-size: 23px;
    font-weight: 700;
    color: var(--text-soft);
    letter-spacing: 0.3px;
  }
  .brand-mark {
    position: absolute;
    left: 243px;
    top: 180px;
    width: 300px;
    height: 300px;
    border-radius: 50%;
    background: var(--mark-grey);
  }
  .brand-name {
    top: 655px;
    font-family: "Questrial", Arial, sans-serif;
    font-weight: 400;
    color: var(--text-white);
    font-size: 54px;
    letter-spacing: 9px;
    line-height: 1;
    padding-left: 9px;
  }
  .brand-sub {
    top: 722px;
    font-family: "Questrial", Arial, sans-serif;
    font-weight: 400;
    color: var(--text-white);
    font-size: 24px;
    letter-spacing: 4px;
    padding-left: 4px;
  }
  .tagline {
    top: 782px;
    font-size: 31px;
    font-weight: 700;
    color: var(--text-white);
  }
  .tagline-rule {
    position: absolute;
    left: 93px;
    top: 828px;
    width: 601px;
    height: 1px;
    background: var(--rule);
  }
  .one-night {
    top: 840px;
    font-size: 46px;
    font-weight: 700;
    color: var(--accent-red);
    text-shadow: 0 0 14px var(--accent-glow), 0 0 4px var(--accent-glow);
  }
  .event-date {
    top: 903px;
    font-size: 26px;
    font-weight: 700;
    color: var(--text-grey);
    letter-spacing: 0.5px;
  }
  .invite {
    top: 1010px;
    font-size: 24px;
    font-weight: 700;
    color: var(--text-white);
  }
  .invite-note {
    top: 1056px;
    font-size: 11px;
    font-weight: 600;
    color: var(--text-soft);
  }
  .host {
    position: absolute;
    left: 0;
    top: 1104px;
    width: 100%;
    display: flex;
    justify-content: center;
    align-items: center;
    gap: 14px;
  }
  .host__dot {
    width: 34px;
    height: 34px;
    border-radius: 50%;
    background: var(--text-grey);
  }
  .host__name {
    font-family: "Questrial", Arial, sans-serif;
    font-size: 30px;
    color: var(--text-soft);
    letter-spacing: 1px;
  }
</style>
</head>
<body>
  <main class="flyer">
    <div class="flyer__pattern" role="img" aria-label="Dark black damask scroll pattern background"></div>

    <p class="flyer__block presenter">VELVETROLL ATLANTA PRESENTS</p>

    <div class="brand-mark" aria-hidden="true"></div>
    <p class="flyer__block brand-name">LANTERN</p>
    <p class="flyer__block brand-sub">NIGHTCLUB</p>

    <p class="flyer__block tagline">A POPUP NIGHTCLUB EXPERIENCE</p>
    <div class="tagline-rule"></div>
    <p class="flyer__block one-night">FOR ONE NIGHT ONLY</p>
    <p class="flyer__block event-date">FRIDAY OCTOBER 18 2013 @ 9:00PM</p>

    <p class="flyer__block invite">INVITE ONLY</p>
    <p class="flyer__block invite-note">SEE INVITATION FOR LOCATION DETAILS</p>

    <div class="host">
      <span class="host__dot" aria-hidden="true"></span>
      <span class="host__name">VELVETROLL ATLANTA</span>
    </div>
  </main>
</body>
</html>
```